Business Card Design

New business card design

Target Market(s)

Residential & Commercial Property Managers

Industry/Entity Type

Plumbing Services

Contact Information for Business Card

Name - Rowan Keddle, title - Director, Phone Number - 0431 286 517, email - rowan@tbk-plumbing.com.au, Company ABN - 73 215 904 386,

Font styles to use
Sans Serif

Colors
0054AA
0677BA
7BADD7
CADEEF
E8F1F8

```html
<!DOCTYPE html>
<html lang="en">
<head>
<meta charset="utf-8">
<title>TBK Plumbing Services – Business Card</title>
<link rel="stylesheet" href="https://fonts.googleapis.com/css2?family=Montserrat:wght@300;400;500;700&display=swap">
<style>
  :root {
    --bg: #e6e8ea;
    --ink: #1f252b;
    --ink-soft: #2b3239;
    --ink-lift: #39424b;
    --paper: #ffffff;
    --sky: #29abe2;
    --mute: #8a8580;
  }
  * { box-sizing: border-box; margin: 0; padding: 0; }
  html, body { width: 1200px; height: 912px; overflow: hidden; }
  body {
    background: var(--bg);
    font-family: "Montserrat", sans-serif;
    position: relative;
  }
  .card {
    position: absolute;
    width: 620px;
    height: 372px;
    border-radius: 22px;
    overflow: hidden;
    box-shadow: 0 10px 30px rgba(0,0,0,.18);
  }
  .card--back { left: 70px; top: 60px; background: var(--ink); }
  .card--front { left: 510px; top: 480px; background: var(--paper); }

  .wordmark {
    position: absolute;
    display: flex;
    flex-direction: column;
    align-items: center;
    gap: 8px;
  }
  .wordmark__row { display: flex; align-items: center; gap: 10px; }
  .wordmark__name {
    font-weight: 500;
    font-size: 46px;
    letter-spacing: 2px;
    line-height: 1;
  }
  .wordmark__dot { width: 14px; height: 14px; border-radius: 50%; background: var(--sky); }
  .wordmark__tag {
    font-weight: 300;
    font-size: 13px;
    letter-spacing: 9px;
    color: var(--mute);
  }
  .card--back .wordmark { left: 0; right: 0; top: 130px; }
  .card--back .wordmark__name { color: var(--ink-lift); }
  .card--back .wordmark__tag { color: var(--ink-soft); }

  .card--front .wordmark { left: 170px; right: 20px; top: 62px; }
  .card--front .wordmark__name { color: var(--ink); }

  .band-dark {
    position: absolute; left: 0; top: 232px; width: 340px; height: 100px;
    background: var(--ink);
  }
  .band-sky {
    position: absolute; left: 340px; top: 196px; right: 0; height: 136px;
    background: var(--sky);
  }
  .person {
    position: absolute; right: 22px; top: 22px; text-align right;
    text-align: right;
  }
  .person__name { color: var(--sky); font-weight: 700; font-size: 30px; line-height: 1.1; white-space: nowrap; }
  .person__title { color: var(--paper); font-weight: 400; font-size: 17px; }
  .contacts {
    position: absolute; left: 20px; right: 14px; top: 24px;
    color: var(--paper); font-size: 15px; font-weight: 400;
    display: flex; flex-direction: column; gap: 10px;
  }
  .contacts__item { display: flex; align-items: center; gap: 7px; white-space: nowrap; }
  .contacts__item svg { width: 14px; height: 14px; flex: none; }
  .contacts__item--email { font-size: 14px; }
</style>
</head>
<body>
  <section class="card card--back" aria-label="Business card, back">
    <div class="wordmark">
      <div class="wordmark__row">
        <span class="wordmark__name">TBK Plumbing</span>
        <span class="wordmark__dot"></span>
      </div>
      <span class="wordmark__tag">plumbing services</span>
    </div>
  </section>

  <section class="card card--front" aria-label="Business card, front">
    <div class="wordmark">
      <div class="wordmark__row">
        <span class="wordmark__name">TBK Plumbing</span>
        <span class="wordmark__dot"></span>
      </div>
      <span class="wordmark__tag">plumbing services</span>
    </div>

    <div class="band-dark">
      <div class="person">
        <p class="person__name">Rowan Keddle</p>
        <p class="person__title">Director</p>
      </div>
    </div>

    <div class="band-sky">
      <div class="contacts">
        <p class="contacts__item">ABN - 73 215 904 386</p>
        <p class="contacts__item">
          <svg viewBox="0 0 24 24" aria-hidden="true"><path fill="#fff" d="M6.6 10.8a15.1 15.1 0 0 0 6.6 6.6l2.2-2.2a1 1 0 0 1 1-.25 11.4 11.4 0 0 0 3.6.57 1 1 0 0 1 1 1V20a1 1 0 0 1-1 1A17 17 0 0 1 3 4a1 1 0 0 1 1-1h3.5a1 1 0 0 1 1 1c0 1.25.2 2.45.57 3.57a1 1 0 0 1-.25 1z"/></svg>
          0431 286 517
        </p>
        <p class="contacts__item contacts__item--email">
          <svg viewBox="0 0 24 24" aria-hidden="true"><rect x="2" y="5" width="20" height="14" rx="1.5" fill="#fff"/><path d="M3 6l9 7 9-7" fill="none" stroke="#29abe2" stroke-width="1.8"/></svg>
          rowan@tbk-plumbing.com.au
        </p>
      </div>
    </div>
  </section>
</body>
</html>
```